Sparrow Haulage needs a business card design.

Design a double-sided business card for new freight business. On the front, would like to see our logo along with the following info:

Martin Obuya
CEO/FOUNDER
555-206-7142
martinobuya@sparrow-haulage.example

On the reverse side, we would like to use the graphic image of our logo only without the Sparrow Haulage name.

```html
<!DOCTYPE html>
<html lang="en">
<head>
<meta charset="utf-8">
<title>Sparrow Haulage – Business Card</title>
<link rel="stylesheet" href="https://fonts.googleapis.com/css2?family=Open+Sans:wght@400;700&display=swap">
<style>
  :root {
    --stage: #2a2a2c;
    --navy: #1b1957;
    --navy-soft: #24226a;
    --red: #b71f27;
    --white: #ffffff;
  }
  * { box-sizing: border-box; margin: 0; padding: 0; }
  html, body {
    width: 1200px; height: 900px; overflow: hidden;
    background: var(--stage);
    font-family: "Open Sans", sans-serif;
  }
  .card {
    position: absolute;
    left: 320px;
    width: 560px; height: 320px;
    border-radius: 14px;
    overflow: hidden;
    background: var(--navy);
  }
  .card--back { top: 90px; }
  .card--front { top: 480px; }

  .card-back__mark {
    position: absolute; left: 50%; top: 50%;
    width: 130px; height: 130px; margin: -65px 0 0 -65px;
    border-radius: 50%;
    background: var(--navy-soft);
  }

  .card-front__shape { position: absolute; inset: 0; }

  .holder { position: absolute; left: 34px; top: 30px; color: var(--white); }
  .holder__name { font-weight: 700; font-size: 21px; line-height: 1.1; white-space: nowrap; }
  .holder__title { font-weight: 400; font-size: 11.5px; letter-spacing: .3px; margin-top: 2px; }

  .contacts {
    position: absolute; left: 34px; bottom: 30px;
    list-style: none; color: var(--white); font-size: 12.5px;
  }
  .contacts__item { display: flex; align-items: center; gap: 8px; line-height: 20px; white-space: nowrap; }
  .contacts__icon { width: 12px; height: 12px; fill: var(--white); flex: none; }

  .brand {
    position: absolute; left: 322px; top: 146px;
    display: flex; align-items: center; gap: 8px;
    font-weight: 700; font-size: 17px; letter-spacing: 1.5px;
    color: var(--navy); text-transform: uppercase;
    white-space: nowrap;
  }
  .brand__dot { width: 12px; height: 12px; border-radius: 50%; background: var(--red); flex: none; }
</style>
</head>
<body>

<section class="card card--back" aria-label="Card back">
  <span class="card-back__mark" aria-hidden="true"></span>
</section>

<section class="card card--front" aria-label="Card front">
  <svg class="card-front__shape" viewBox="0 0 560 320" aria-hidden="true">
    <path d="M340 0 L560 0 L560 320 L410 320 L272 178 Q250 150 285 125 Z" fill="var(--red)"/>
    <path d="M385 0 L560 0 L560 320 L455 320 L310 178 Q290 150 322 128 Z" fill="var(--white)"/>
  </svg>

  <div class="holder">
    <p class="holder__name">Martin Obuya</p>
    <p class="holder__title">CEO/FOUNDER</p>
  </div>

  <ul class="contacts">
    <li class="contacts__item">
      <svg class="contacts__icon" viewBox="0 0 24 24"><path d="M6.6 10.8a15.1 15.1 0 0 0 6.6 6.6l2.2-2.2a1 1 0 0 1 1-.25 11.4 11.4 0 0 0 3.6.57 1 1 0 0 1 1 1V20a1 1 0 0 1-1 1A17 17 0 0 1 3 4a1 1 0 0 1 1-1h3.5a1 1 0 0 1 1 1c0 1.25.2 2.45.57 3.57a1 1 0 0 1-.25 1z"/></svg>
      555-206-7142
    </li>
    <li class="contacts__item">
      <svg class="contacts__icon" viewBox="0 0 24 24"><path d="M2 5h20v14H2z M3.5 6.5 12 13l8.5-6.5" fill="none" stroke="var(--white)" stroke-width="2"/></svg>
      martinobuya@sparrow-haulage.example
    </li>
    <li class="contacts__item">
      <svg class="contacts__icon" viewBox="0 0 24 24"><circle cx="12" cy="12" r="9" fill="none" stroke="var(--white)" stroke-width="2"/><path d="M3 12h18M12 3c3 3 3 15 0 18M12 3c-3 3-3 15 0 18" fill="none" stroke="var(--white)" stroke-width="1.5"/></svg>
      www.sparrow-haulage.example
    </li>
  </ul>

  <div class="brand">
    <span class="brand__dot" aria-hidden="true"></span>
    <span class="brand__name">Sparrow Haulage</span>
  </div>
</section>

</body>
</html>
```